Stylish Business Cards Wanted

- DOUBLE SIDED Design Required -

High end, edgy cards for a corporate and personal stylist. Must include logo,
Name: Belinda Harwick
Title: Director and Stylist
telephone : +61 8 7142 5809
email: belinda@theloombriefing.example
website: theloombriefing.example
Tag: Corporate Workwear & Uniform Specialist | Personal Stylist
Would like nice icons for telephone, email, website

Target Market(s)

Businesses wanting stylish uniforms, people wanting stylish wardrobes

Industry/Entity Type

Corporate Workwear Stylist

Contact Information for Business Card

I would like black, white and gold foiling incorporated in the design - possibly a touch of the other colours on my branding guide attached Name: Belinda Harwick Title: Director and Stylist telephone : +61 8 7142 5809 email: belinda@theloombriefing.example website: theloombriefing.example Tag: Corporate Workwear & Uniform Specialist | Personal Stylist Would like nice icons for telephone, email, website

Font styles to use
Other font styles liked:
• Raleway

Colors

Designer to choose colors to be used in the design.

Requirements
Must have
• Gold foil accents

```html
<!DOCTYPE html>
<html lang="en">
<head>
<meta charset="utf-8">
<title>The Loom Briefing – Business Cards</title>
<link href="https://fonts.googleapis.com/css2?family=Montserrat:wght@400;500;600&display=swap" rel="stylesheet">
<style>
  :root {
    --backdrop: #dcdcdc;
    --ink: #111111;
    --card-white: #ffffff;
    --gold: #e7bb3f;
    --gold-deep: #c99a22;
    --pattern-black: #121212;
  }
  * { box-sizing: border-box; margin: 0; padding: 0; }
  html, body {
    width: 1200px; height: 900px; overflow: hidden;
    background: var(--backdrop);
    font-family: "Montserrat", Arial, sans-serif;
  }
  .card {
    position: absolute; left: 250px;
    width: 700px; height: 400px;
    box-shadow: 0 6px 14px rgba(0,0,0,0.22);
    border-bottom: 5px solid var(--gold);
  }
  .card--back { top: 36px; background: var(--pattern-black); }
  .card--front { top: 468px; background: var(--card-white); }

  .back-pattern { position: absolute; inset: 0; background: linear-gradient(135deg, #1b1d1d, #0c0c0c); }
  .back-mark {
    position: absolute; left: 0; right: 0; top: 176px;
    text-align: center; color: var(--gold);
    font-weight: 600; font-size: 26px; letter-spacing: 1px;
  }

  .brand {
    position: absolute; right: 44px; top: 70px; width: 300px;
    text-align: center; color: var(--ink);
    font-weight: 600; font-size: 34px; line-height: 1.15; letter-spacing: 1px;
  }
  .person { position: absolute; left: 40px; top: 170px; padding-left: 22px; }
  .person::before {
    content: ""; position: absolute; left: 0; top: 4px;
    width: 8px; height: 42px; background: var(--gold); border-radius: 2px;
  }
  .person__name { font-size: 27px; font-weight: 500; color: var(--ink); line-height: 1.1; }
  .person__title { font-size: 13px; color: var(--gold); margin-top: 2px; }

  .contacts { position: absolute; left: 56px; top: 248px; list-style: none; }
  .contacts li { display: flex; align-items: center; gap: 14px; height: 28px; font-size: 15px; color: var(--ink); }
  .contacts svg { width: 20px; height: 20px; flex: none; }

  .tagline {
    position: absolute; left: 0; right: 0; bottom: 16px; height: 42px;
    background: var(--ink);
    border-top: 3px solid var(--gold);
    box-shadow: 0 -6px 0 var(--card-white), 0 -8px 0 var(--gold);
    display: flex; align-items: center; justify-content: center; gap: 14px;
    color: var(--gold); font-size: 17px; font-weight: 500; letter-spacing: 0.3px;
  }
  .tagline__sep { color: var(--card-white); }
</style>
</head>
<body>
  <section class="card card--back">
    <div class="back-pattern" role="img" aria-label="Repeating faint brand pattern on black"></div>
    <div class="back-mark">The Loom Briefing</div>
  </section>

  <section class="card card--front">
    <div class="brand">The Loom Briefing</div>

    <div class="person">
      <p class="person__name">Belinda Harwick</p>
      <p class="person__title">Director and Stylist</p>
    </div>

    <ul class="contacts">
      <li>
        <svg viewBox="0 0 20 20"><circle cx="10" cy="10" r="10" fill="#111"/><path d="M7 5.5l1.6 2.3-1 1.1a7 7 0 0 0 3.5 3.5l1.1-1 2.3 1.6-.9 1.5c-3.8.2-8.2-4.2-8-8z" fill="#e7bb3f"/></svg>
        +61 8 7142 5809
      </li>
      <li>
        <svg viewBox="0 0 20 20"><circle cx="10" cy="10" r="10" fill="#111"/><rect x="5" y="6.5" width="10" height="7" fill="#e7bb3f"/><path d="M5 6.5l5 4 5-4" fill="none" stroke="#111" stroke-width="1"/></svg>
        belinda@theloombriefing.example
      </li>
      <li>
        <svg viewBox="0 0 20 20"><circle cx="10" cy="10" r="10" fill="#111"/><circle cx="10" cy="10" r="5" fill="none" stroke="#e7bb3f" stroke-width="1.3"/><ellipse cx="10" cy="10" rx="2" ry="5" fill="none" stroke="#e7bb3f" stroke-width="1.1"/><path d="M5 10h10" stroke="#e7bb3f" stroke-width="1.1"/></svg>
        www.theloombriefing.example
      </li>
    </ul>

    <div class="tagline">
      <span>CORPORATE WORKWEAR</span><span class="tagline__sep">|</span>
      <span>UNIFORM SPECIALIST</span><span class="tagline__sep">|</span>
      <span>PERSONAL STYLIST</span>
    </div>
  </section>
</body>
</html>
```